VFX Company Business Card Design Project

The Kestrel Works is a decentralized Visual Effects Studio servicing the television and feature film industries.
Project Brief:
Take our logo that was previously designed on Pencil Harbor and make a double sided business card.
Requirements:
- Card MUST be double sided.
- Front of card MUST have the yellow part of our logo against the dark grey background.
- Back of card is completely up to the designer.
- Back of card must include the complete company logo.
Please follow these File Preparation guidelines:
http://printnook.ca/infopage?file=filetype_en&s=PrintNook_new&lang=en
Business

```html
<!DOCTYPE html>
<html lang="en">
<head>
<meta charset="utf-8">
<title>The Kestrel Works – Business Card</title>
<link rel="stylesheet" href="https://fonts.googleapis.com/css2?family=Exo+2:wght@300;400;600;700&display=swap">
<style>
  :root {
    --stage: #1c1c1d;
    --card-dark: #242424;
    --yellow: #ffc627;
    --yellow-deep: #f2b81c;
    --slate: #68737a;
    --ink: #1e1e1e;
    --light: #e8e8e8;
  }
  html, body {
    margin: 0;
    padding: 0;
    width: 1200px;
    height: 900px;
    overflow: hidden;
    background: var(--stage);
    font-family: "Exo 2", sans-serif;
  }
  .canvas {
    position: relative;
    width: 1200px;
    height: 900px;
  }
  .card {
    position: absolute;
    top: 302px;
    width: 520px;
    height: 296px;
    overflow: hidden;
    box-shadow: 0 18px 40px rgba(0,0,0,.55);
  }

  /* Front */
  .card-front { left: 60px; background: var(--card-dark); }
  .brand {
    display: flex;
    align-items: center;
    gap: 12px;
    color: var(--yellow);
    font-weight: 600;
    letter-spacing: .04em;
    white-space: nowrap;
  }
  .brand-dot {
    border-radius: 50%;
    background: var(--yellow);
    flex: none;
  }
  .card-front .brand { position: absolute; left: 36px; top: 34px; font-size: 24px; }
  .card-front .brand-dot { width: 22px; height: 22px; }

  .info-band {
    position: absolute;
    left: 0; right: 0;
    top: 96px;
    height: 118px;
    background: var(--yellow);
    border-bottom: 6px solid var(--slate);
    padding: 16px 30px 0;
    box-sizing: border-box;
    color: var(--ink);
  }
  .person { margin: 0 0 12px; font-size: 19px; font-weight: 300; letter-spacing: .02em; }
  .person strong { font-weight: 700; }
  .role {
    font-size: 12px;
    font-weight: 400;
    padding-left: 8px;
    margin-left: 6px;
    border-left: 1px solid var(--ink);
    letter-spacing: 0;
  }
  .contacts {
    display: grid;
    grid-template-columns: 130px 130px 1fr;
    row-gap: 6px;
    column-gap: 14px;
    font-size: 12px;
  }
  .contact { display: flex; align-items: center; gap: 6px; white-space: nowrap; }
  .contact svg { width: 12px; height: 12px; flex: none; }

  /* Back */
  .card-back { left: 620px; background: var(--yellow); }
  .pattern-field {
    position: absolute;
    inset: 0;
    background: linear-gradient(135deg, var(--yellow) 0%, var(--yellow-deep) 100%);
  }
  .logo-band {
    position: absolute;
    left: 0; right: 0;
    top: 112px;
    height: 108px;
    background: var(--card-dark);
    border-top: 5px solid var(--slate);
    border-bottom: 5px solid var(--slate);
    display: flex;
    align-items: center;
    justify-content: center;
  }
  .card-back .brand { font-size: 34px; gap: 16px; }
  .card-back .brand-dot { width: 30px; height: 30px; }
  .web {
    position: absolute;
    left: 0; right: 0;
    top: 240px;
    text-align: center;
    color: var(--ink);
    font-size: 13px;
    font-weight: 600;
    letter-spacing: .32em;
  }
</style>
</head>
<body>
<main class="canvas">

  <section class="card card-front" aria-label="Card front">
    <div class="brand"><span class="brand-dot"></span>The Kestrel Works</div>

    <div class="info-band">
      <p class="person">MARCUS <strong>ELDEN</strong><span class="role">Managing Director</span></p>
      <div class="contacts">
        <span class="contact">
          <svg viewBox="0 0 12 12"><rect width="12" height="12" rx="2" fill="#1e1e1e"/><path d="M4 3c-1 1-1 3 1 5s4 2 5 1l-1.3-1.3-1 .7c-.8-.3-1.8-1.3-2.1-2.1l.7-1z" fill="#ffc627"/></svg>
          +00 123 48 20 617
        </span>
        <span class="contact">
          <svg viewBox="0 0 12 12"><rect width="12" height="12" rx="2" fill="#1e1e1e"/><path d="M4 3c-1 1-1 3 1 5s4 2 5 1l-1.3-1.3-1 .7c-.8-.3-1.8-1.3-2.1-2.1l.7-1z" fill="#ffc627"/></svg>
          +00 123 48 20 617
        </span>
        <span class="contact">
          <svg viewBox="0 0 12 12"><rect width="12" height="12" rx="2" fill="#1e1e1e"/><path d="M2.5 4h7v4.5h-7z" fill="none" stroke="#ffc627" stroke-width="1"/><path d="M2.5 4l3.5 2.6L9.5 4" fill="none" stroke="#ffc627" stroke-width="1"/></svg>
          info@kestrelworks.net
        </span>
        <span class="contact">
          <svg viewBox="0 0 12 12"><rect width="12" height="12" rx="2" fill="#1e1e1e"/><path d="M4 3c-1 1-1 3 1 5s4 2 5 1l-1.3-1.3-1 .7c-.8-.3-1.8-1.3-2.1-2.1l.7-1z" fill="#ffc627"/></svg>
          +00 123 48 20 617
        </span>
        <span class="contact">
          <svg viewBox="0 0 12 12"><rect width="12" height="12" rx="2" fill="#1e1e1e"/><path d="M4 3c-1 1-1 3 1 5s4 2 5 1l-1.3-1.3-1 .7c-.8-.3-1.8-1.3-2.1-2.1l.7-1z" fill="#ffc627"/></svg>
          +00 123 48 20 617
        </span>
        <span class="contact">
          <svg viewBox="0 0 12 12"><rect width="12" height="12" rx="2" fill="#1e1e1e"/><circle cx="6" cy="6" r="3.3" fill="none" stroke="#ffc627" stroke-width="1"/><path d="M2.7 6h6.6M6 2.7c-1.5 2-1.5 4.6 0 6.6M6 2.7c1.5 2 1.5 4.6 0 6.6" fill="none" stroke="#ffc627" stroke-width=".8"/></svg>
          www.kestrelworks.net
        </span>
      </div>
    </div>
  </section>

  <section class="card card-back" aria-label="Card back">
    <div class="pattern-field" role="img" aria-label="Repeating company name pattern in tone-on-tone yellow"></div>
    <div class="logo-band">
      <div class="brand"><span class="brand-dot"></span>The Kestrel Works</div>
    </div>
    <p class="web">WWW.KESTRELWORKS.NET</p>
  </section>

</main>
</body>
</html>
```